Ridgeline Journeys business card

please see website
www.ridgelinejourneys.comau

info needed on card
Curtis Halvey
Ph
email
Adventure Riding GPS trails

please use my logo and colours off my site

Curtis Halvey
curtis@ridgelinejourneys.com

```html
<!DOCTYPE html>
<html lang="en">
<head>
<meta charset="utf-8">
<title>Ridgeline Journeys – Business Card</title>
<link rel="stylesheet" href="https://fonts.googleapis.com/css2?family=Open+Sans:wght@400;800&display=swap">
<style>
  :root {
    --bg: #1c1c1c;
    --yellow: #f2ea4a;
    --yellow-deep: #e4dc3a;
    --yellow-pale: #fbf8d4;
    --white: #ffffff;
    --ink: #1a1a1a;
    --grey: #4a4a4a;
    --edge-grey: #d9d9d9;
  }
  * { margin: 0; padding: 0; box-sizing: border-box; }
  html, body {
    width: 1200px; height: 922px; overflow: hidden;
    background: var(--bg);
    font-family: "Open Sans", Arial, sans-serif;
  }
  .canvas { position: relative; width: 1200px; height: 922px; }

  .card {
    position: absolute;
    width: 640px; height: 366px;
    border-radius: 14px;
    overflow: hidden;
  }

  /* Front face */
  .card-front {
    left: 60px; top: 60px;
    background: radial-gradient(ellipse at 50% 20%, var(--white) 0%, var(--yellow-pale) 35%, var(--yellow-deep) 100%);
  }
  .brand {
    position: absolute;
    display: flex; align-items: center; gap: 22px;
    color: var(--ink);
    font-weight: 800;
    text-transform: uppercase;
    line-height: 1.02;
    letter-spacing: 0.5px;
  }
  .brand-dot {
    flex: none;
    border-radius: 50%;
    background: var(--ink);
  }
  .card-front .brand { left: 120px; top: 126px; font-size: 46px; }
  .card-front .brand-dot { width: 64px; height: 64px; }

  /* Back face */
  .card-back { right: 60px; top: 496px; background: var(--yellow); }
  .card-back .wave { position: absolute; inset: 0; width: 100%; height: 100%; }
  .card-back .brand { left: 290px; top: 78px; font-size: 36px; }
  .card-back .brand-dot { width: 48px; height: 48px; }
  .holder-name {
    position: absolute; right: 40px; top: 226px;
    font-size: 30px; font-weight: 400; color: var(--grey);
  }
  .contact-list {
    position: absolute; left: 30px; bottom: 34px;
    list-style: none;
    font-size: 15px; color: var(--ink);
  }
  .contact-list li { display: flex; align-items: center; gap: 12px; margin-top: 6px; }
  .contact-list svg { width: 16px; height: 14px; flex: none; }
</style>
</head>
<body>
<main class="canvas">

  <section class="card card-front" aria-label="Business card front">
    <div class="brand">
      <span class="brand-dot"></span>
      <span>Ridgeline<br>Journeys</span>
    </div>
  </section>

  <section class="card card-back" aria-label="Business card back">
    <svg class="wave" viewBox="0 0 640 366" preserveAspectRatio="none" aria-hidden="true">
      <path d="M200 0 C 250 40, 260 160, 330 250 C 390 320, 520 330, 640 316 L640 338 C 500 356, 360 336, 300 262 C 240 180, 230 60, 190 0 Z" fill="var(--edge-grey)"/>
      <path d="M200 0 C 250 40, 260 160, 330 250 C 390 320, 520 320, 640 300 L640 318 C 510 334, 380 320, 318 250 C 250 168, 246 50, 200 0 Z" fill="var(--ink)"/>
      <path d="M200 0 L640 0 L640 300 C 520 320, 400 312, 335 245 C 268 170, 250 40, 200 0 Z" fill="var(--white)"/>
    </svg>
    <div class="brand">
      <span class="brand-dot"></span>
      <span>Ridgeline<br>Journeys</span>
    </div>
    <p class="holder-name">Curtis Halvey</p>
    <ul class="contact-list">
      <li>
        <svg viewBox="0 0 16 14" aria-hidden="true"><rect width="16" height="14" rx="2" fill="var(--ink)"/><path d="M3 4 L8 8 L13 4" stroke="var(--yellow)" stroke-width="1.5" fill="none"/></svg>
        curtis@ridgelinejourneys.com
      </li>
      <li>
        <svg viewBox="0 0 16 14" aria-hidden="true"><rect width="16" height="14" rx="2" fill="var(--ink)"/><circle cx="8" cy="7" r="4.5" stroke="var(--yellow)" stroke-width="1.3" fill="none"/><path d="M3.5 7 H12.5 M8 2.5 V11.5" stroke="var(--yellow)" stroke-width="1"/></svg>
        www.ridgelinejourneys.com.au
      </li>
    </ul>
  </section>

</main>
</body>
</html>
```